BRISKEL Need a luxury modern business card designed.

Need a luxury modern business card designed. refer to the uploaded files for the company name and logo in the zip file under source files. i will making my descion on monday. so please send in before then so if we need to edit we will have the time. we have a trade show coming up and im on a deadline for printer.

Target Market(s)

high end clients

Contact Information for Business Card

Company nAme and logo. Tobias Fennick Co-Founder / Project Manager Office # 555-318-7094 Cell # 555-642-1586 BRISKEL.CA Tobias@briskel-example.ca

Font styles to use
Other font styles liked:
• Modern

Requirements
Must have
• Company name and logo, contact info, using the black, gold and white color scheme.

```html
<!DOCTYPE html>
<html lang="en">
<head>
<meta charset="utf-8">
<title>BRISKEL Business Card</title>
<link href="https://fonts.googleapis.com/css2?family=Montserrat:wght@300;400;500&display=swap" rel="stylesheet">
<style>
  :root {
    --stage: #1c1c1c;
    --card-dark: #2f2f2f;
    --card-light: #ffffff;
    --gold: #a8945a;
    --ink: #2a2a2a;
    --white: #f4f4f4;
  }
  * { box-sizing: border-box; margin: 0; padding: 0; }
  html, body {
    width: 1200px; height: 900px; overflow: hidden;
    background: var(--stage);
    font-family: "Montserrat", sans-serif;
  }
  .canvas {
    position: relative; width: 1200px; height: 900px;
  }
  .card {
    position: absolute; left: 250px; width: 700px; height: 400px;
    border-left: 3px solid var(--gold);
    border-bottom: 3px solid var(--gold);
    box-shadow: 0 12px 30px rgba(0,0,0,.55);
  }
  /* Back side */
  .card-back {
    top: 35px; background: var(--card-dark);
  }
  .card-back .wordmark {
    position: absolute; right: 50px; top: 80px;
    color: var(--white); font-weight: 300; font-size: 46px; letter-spacing: 10px;
    display: flex; align-items: center; gap: 18px;
  }
  .wordmark .mark-square {
    width: 18px; height: 18px; background: var(--gold); display: inline-block;
  }
  /* Front side */
  .card-front {
    top: 465px; background: var(--card-light);
  }
  .card-front .wordmark {
    position: absolute; left: 0; right: 0; top: 70px;
    display: flex; justify-content: center; align-items: center; gap: 14px;
    color: var(--ink); font-weight: 300; font-size: 40px; letter-spacing: 9px;
  }
  .rule {
    position: absolute; left: 70px; right: 70px; top: 170px;
    height: 1.5px; background: var(--gold);
  }
  .person {
    position: absolute; right: 370px; top: 225px; text-align: right;
  }
  .person-name {
    color: var(--gold); font-weight: 500; font-size: 26px; letter-spacing: 1px;
    text-transform: uppercase;
  }
  .person-title {
    color: var(--ink); font-size: 18px; margin-top: 4px;
  }
  .divider {
    position: absolute; left: 350px; top: 215px; width: 1.5px; height: 115px;
    background: var(--gold);
  }
  .contacts {
    position: absolute; left: 375px; top: 212px; list-style: none;
  }
  .contacts li {
    display: flex; align-items: center; gap: 12px;
    color: var(--ink); font-size: 19px; line-height: 30px;
  }
  .contacts svg { width: 18px; height: 18px; flex: none; }
  .contacts .accent { color: var(--gold); font-weight: 500; }
</style>
</head>
<body>
<main class="canvas">
  <section class="card card-back" aria-label="Card back">
    <div class="wordmark"><span class="mark-square"></span>BRISKEL</div>
  </section>

  <section class="card card-front" aria-label="Card front">
    <div class="wordmark"><span class="mark-square"></span>BRISKEL</div>
    <div class="rule"></div>

    <div class="person">
      <p class="person-name">Tobias Fennick</p>
      <p class="person-title">Co-Founder | Project Manager</p>
    </div>

    <div class="divider"></div>

    <ul class="contacts">
      <li>
        <svg viewBox="0 0 20 20" fill="none" stroke="var(--gold)" stroke-width="1.4">
          <circle cx="10" cy="10" r="8.3"/>
          <path d="M7 6.2c-.6.5-.7 1.6.2 3.2s2.3 3 3.7 3.5c1 .3 1.7 0 2-.6l-1.3-1.2-.9.5c-.8-.4-1.6-1.2-2-2l.5-.9L8 6z"/>
        </svg>
        555-318-7094
      </li>
      <li>
        <svg viewBox="0 0 20 20" fill="none" stroke="var(--gold)" stroke-width="1.4">
          <rect x="5.5" y="2" width="9" height="16" rx="1.5"/>
          <line x1="9" y1="15.5" x2="11" y2="15.5"/>
        </svg>
        555-642-1586
      </li>
      <li>
        <svg viewBox="0 0 20 20" fill="none" stroke="var(--gold)" stroke-width="1.4">
          <rect x="2" y="4.5" width="16" height="11"/>
          <path d="M2 4.5l8 6.5 8-6.5"/>
        </svg>
        Tobias@briskel-example.ca
      </li>
      <li>
        <svg viewBox="0 0 20 20" fill="none" stroke="var(--gold)" stroke-width="1.4">
          <circle cx="10" cy="10" r="8"/>
          <ellipse cx="10" cy="10" rx="3.5" ry="8"/>
          <line x1="2" y1="10" x2="18" y2="10"/>
        </svg>
        <span>www.<span class="accent">briskel</span>.ca</span>
      </li>
    </ul>
  </section>
</main>
</body>
</html>
```